Veranix - Solution provider in business consulting

Veranix is a swiss based company providing solutions for developing markets. The business covers various fields of business consulting, such as supply chain, product costs, quality management and manufacturing management. The Business operates in a efficient, straight and solution oriented manner.
The final design should communicate these characteristics. Asian people as well as as western people shall identify the qualities of the company at first sight.
The customer needs business cards with a simple view but an recognizable design, printed in high quality. Engraved elements such as the globe or simple words are possible.
Available colors are: (RAL)
102/102/102
51/102/102
153/204/153
255/102/51
Font: Calibri

```html
<!DOCTYPE html>
<html lang="en">
<head>
<meta charset="utf-8">
<title>Veranix – Business Card</title>
<link rel="stylesheet" href="https://fonts.googleapis.com/css2?family=Carlito:wght@400;700&display=swap">
<style>
  :root {
    --page-bg: #d9d6d1;
    --card-top: #767676;
    --card-bottom: #555555;
    --ink: #ffffff;
    --ink-soft: #e6e6e6;
    --rule: rgba(255,255,255,0.55);
  }
  html, body {
    margin: 0;
    padding: 0;
    width: 1200px;
    height: 1022px;
    overflow: hidden;
    background: var(--page-bg);
    font-family: "Carlito", "Calibri", sans-serif;
  }
  .canvas {
    position: relative;
    width: 1200px;
    height: 1022px;
  }
  .card {
    position: absolute;
    left: 100px;
    top: 225px;
    width: 1000px;
    height: 572px;
    border-radius: 26px;
    background: linear-gradient(160deg, var(--card-top) 0%, #666666 50%, var(--card-bottom) 100%);
    box-shadow: 0 10px 30px rgba(0,0,0,0.25);
    overflow: hidden;
    color: var(--ink);
  }
  .brand {
    position: absolute;
    left: 110px;
    top: 300px;
    display: flex;
    align-items: center;
    gap: 20px;
  }
  .brand-dot {
    width: 54px;
    height: 54px;
    border-radius: 50%;
    background: var(--ink);
  }
  .brand-name {
    font-size: 92px;
    font-weight: 400;
    line-height: 1;
    letter-spacing: 1px;
    color: var(--ink);
  }
  .divider {
    position: absolute;
    left: 545px;
    top: 170px;
    width: 1px;
    height: 260px;
    background: var(--rule);
  }
  .contact {
    position: absolute;
    left: 580px;
    top: 160px;
    font-size: 21px;
    line-height: 1.35;
    color: var(--ink-soft);
  }
  .contact .person {
    font-size: 32px;
    font-weight: 700;
    color: var(--ink);
    margin: 0;
  }
  .contact .role {
    margin: 0 0 14px;
  }
  .contact .address {
    margin: 0 0 14px;
  }
  .contact ul {
    list-style: none;
    margin: 0;
    padding: 0;
  }
  .contact li {
    display: flex;
    align-items: center;
    gap: 12px;
  }
  .contact svg {
    width: 15px;
    height: 15px;
    fill: none;
    stroke: var(--ink);
    stroke-width: 1.8;
  }
</style>
</head>
<body>
<main class="canvas">
  <section class="card">
    <div class="brand">
      <span class="brand-name">Veranix</span>
      <span class="brand-dot"></span>
    </div>

    <div class="divider"></div>

    <div class="contact">
      <p class="person">Marco Keller</p>
      <p class="role">CEO</p>
      <p class="address">Veranix GmbH Lindenhof<br>14 8400 Talwil Switzerland</p>
      <ul>
        <li>
          <svg viewBox="0 0 16 16"><rect x="4" y="1.5" width="8" height="13" rx="1.5"/></svg>
          +41 79 208 3317
        </li>
        <li>
          <svg viewBox="0 0 16 16"><path d="M3 2.5l3 0.5 1 3-2 1.5a8 8 0 0 0 3.5 3.5l1.5-2 3 1 0.5 3c-6 1-12-5-10.5-10.5z"/></svg>
          +41 71 604 5582
        </li>
        <li>
          <svg viewBox="0 0 16 16"><rect x="1.5" y="3.5" width="13" height="9"/><path d="M1.5 3.5l6.5 5 6.5-5"/></svg>
          marco.keller@veranix.ch
        </li>
        <li>
          <svg viewBox="0 0 16 16"><circle cx="8" cy="8" r="6.5"/><path d="M1.5 8h13M8 1.5c-3 3.5-3 9.5 0 13M8 1.5c3 3.5 3 9.5 0 13"/></svg>
          www.veranix.ch
        </li>
      </ul>
    </div>
  </section>
</main>
</body>
</html>
```